Moravel Aesthetic Doctor

I require an elegant, luxurious looking business card for my aesthetic business. I am a doctor and that will set me aside from competitors. I am planning to provide home and spa based treatments to clients with high expectations. I have attached my logo.

```html
<!DOCTYPE html>
<html lang="en">
<head>
<meta charset="UTF-8">
<title>Moravel Aesthetic Doctor – Business Card</title>
<link href="https://fonts.googleapis.com/css2?family=Barlow+Semi+Condensed:wght@600&family=Montserrat:wght@400&family=Roboto:wght@300;400&display=swap" rel="stylesheet">
<style>
  :root {
    --backdrop: #c8c9cb;
    --blue-light: #4ba9dd;
    --blue-deep: #0b5da4;
    --sky: #4aa3d8;
    --band-grey: #9ea3ab;
    --card-white: #f4f5f6;
    --card-grey: #e3e5e7;
    --ink: #2f3033;
    --mark-grey: #7d838e;
    --white: #ffffff;
  }
  * { margin: 0; padding: 0; box-sizing: border-box; }
  html, body { width: 1200px; height: 576px; overflow: hidden; }
  body {
    background: var(--backdrop);
    font-family: "Roboto", Arial, sans-serif;
    position: relative;
  }
  .card {
    position: absolute;
    top: 138px;
    width: 484px;
    height: 294px;
    border-radius: 12px;
    overflow: hidden;
  }

  /* Front */
  .card--front {
    left: 82px;
    background: linear-gradient(160deg, var(--blue-light) 0%, #2a86c9 45%, var(--blue-deep) 100%);
  }
  .brand {
    position: absolute;
    display: flex;
    align-items: center;
    gap: 16px;
  }
  .brand__circle {
    width: 84px; height: 84px;
    border-radius: 50%;
    border: 2px solid currentColor;
    flex: none;
  }
  .brand__name {
    font-family: "Roboto", Arial, sans-serif;
    font-weight: 400;
    text-transform: uppercase;
    line-height: 1;
  }
  .brand__main { display: block; font-size: 50px; letter-spacing: 1px; }
  .brand__sub { display: block; font-size: 20px; letter-spacing: 1.5px; margin-top: 6px; }
  .card--front .brand { left: 44px; top: 46px; color: var(--white); }

  .services {
    position: absolute;
    left: 0; right: 0; top: 196px;
    text-align: center;
    color: var(--white);
    font-weight: 300;
    font-size: 13px;
    line-height: 19px;
  }
  .services .sep { margin: 0 8px; }
  .front-band {
    position: absolute;
    left: 0; right: 0; top: 244px;
    height: 26px;
    background: var(--band-grey);
    color: #eef1f4;
    font-family: "Montserrat", Arial, sans-serif;
    font-size: 12px;
    letter-spacing: 0.8px;
    text-align: center;
    line-height: 26px;
  }

  /* Back */
  .card--back {
    left: 602px;
    background: linear-gradient(135deg, var(--card-white) 0%, var(--card-grey) 100%);
  }
  .silhouette-area {
    position: absolute;
    right: 0; top: 10px;
    width: 170px; height: 250px;
    background: radial-gradient(ellipse at 65% 45%, rgba(190,193,198,0.55) 0%, rgba(210,212,215,0.25) 55%, rgba(230,231,233,0) 80%);
  }
  .card--back .brand { left: 16px; top: 32px; color: var(--mark-grey); }
  .card--back .brand__circle { width: 80px; height: 80px; }
  .card--back .brand__main { font-size: 46px; }
  .card--back .brand__sub { font-size: 19px; }

  .holder {
    position: absolute;
    left: 22px; top: 170px;
    display: flex;
    align-items: baseline;
    width: 430px;
  }
  .holder__name {
    font-family: "Barlow Semi Condensed", Arial, sans-serif;
    font-weight: 600;
    font-size: 17px;
    color: var(--ink);
  }
  .holder__post {
    font-size: 9.5px;
    color: var(--sky);
    margin-left: 5px;
    font-weight: 400;
  }
  .holder__rule {
    flex: 1;
    height: 1px;
    background: #9a9da2;
    margin-left: 6px;
    transform: translateY(-3px);
  }
  .holder__title {
    position: absolute;
    left: 22px; top: 193px;
    font-size: 12.5px;
    color: var(--sky);
  }
  .contacts {
    position: absolute;
    left: 22px; top: 220px;
    display: flex;
    gap: 14px;
    font-size: 12px;
    color: var(--ink);
  }
  .contact { display: flex; align-items: center; gap: 6px; }
  .contact svg { width: 11px; height: 11px; fill: var(--sky); }
  .contact .accent { color: var(--sky); }
  .social {
    position: absolute;
    left: 22px; top: 242px;
    display: flex;
    align-items: center;
    gap: 4px;
    font-size: 12px;
    color: var(--ink);
  }
  .social__dot {
    width: 12px; height: 12px;
    border-radius: 50%;
    background: var(--sky);
    margin-left: 2px;
  }
  .back-tab {
    position: absolute;
    right: 0; bottom: 0;
    width: 266px; height: 38px;
    background: var(--sky);
    clip-path: polygon(18px 0, 100% 0, 100% 100%, 0 100%);
    color: var(--white);
    font-size: 12.5px;
    text-align: right;
    padding-right: 30px;
    line-height: 38px;
  }
</style>
</head>
<body>

  <section class="card card--front">
    <div class="brand">
      <span class="brand__circle"></span>
      <span class="brand__name">
        <span class="brand__main">Moravel</span>
        <span class="brand__sub">Aesthetic Doctor</span>
      </span>
    </div>
    <p class="services">
      Dermal Injectables<span class="sep">|</span>Plasma Facials<span class="sep">|</span>Microneedling<br>
      Skin Boosters<span class="sep">|</span>Excessive Sweating
    </p>
    <div class="front-band">HOME AND SPA BASED TREATMENTS</div>
  </section>

  <section class="card card--back">
    <div class="silhouette-area" role="img" aria-label="Faint decorative profile silhouette in soft grey"></div>
    <div class="brand">
      <span class="brand__circle"></span>
      <span class="brand__name">
        <span class="brand__main">Moravel</span>
        <span class="brand__sub">Aesthetic Doctor</span>
      </span>
    </div>

    <div class="holder">
      <span class="holder__name">Dr Elise Varnholt</span>
      <span class="holder__post">MRCPCH MD</span>
      <span class="holder__rule"></span>
    </div>
    <p class="holder__title">Australasian Diploma of Aesthetic Medicine</p>

    <div class="contacts">
      <span class="contact">
        <svg viewBox="0 0 24 24" aria-hidden="true"><path d="M6.6 10.8a15.1 15.1 0 0 0 6.6 6.6l2.2-2.2a1 1 0 0 1 1-.25 11.4 11.4 0 0 0 3.6.57 1 1 0 0 1 1 1V20a1 1 0 0 1-1 1A17 17 0 0 1 3 4a1 1 0 0 1 1-1h3.5a1 1 0 0 1 1 1c0 1.25.2 2.45.57 3.6a1 1 0 0 1-.25 1z"/></svg>
        0800 555 018
      </span>
      <span class="contact">
        <svg viewBox="0 0 24 24" aria-hidden="true"><path d="M2 5h20v14H2z M4 7v.5l8 5 8-5V7l-8 5z" fill-rule="evenodd"/></svg>
        elise@moravel.co.nz
      </span>
      <span class="contact">
        <svg viewBox="0 0 24 24" aria-hidden="true"><path d="M12 2a10 10 0 1 0 0 20 10 10 0 0 0 0-20zm6.9 6h-2.9a15.6 15.6 0 0 0-1.4-3.6A8 8 0 0 1 18.9 8zM12 4c.8 1.2 1.5 2.5 1.9 4h-3.8c.4-1.5 1.1-2.8 1.9-4zM4.3 14a8 8 0 0 1 0-4h3.4a16 16 0 0 0 0 4zm.8 2h2.9c.3 1.3.8 2.5 1.4 3.6A8 8 0 0 1 5.1 16zM8 8H5.1a8 8 0 0 1 4.3-3.6C8.8 5.5 8.3 6.7 8 8zm4 12c-.8-1.2-1.5-2.5-1.9-4h3.8c-.4 1.5-1.1 2.8-1.9 4zm2.3-6H9.7a14 14 0 0 1 0-4h4.6a14 14 0 0 1 0 4zm.3 5.6c.6-1.1 1.1-2.3 1.4-3.6h2.9a8 8 0 0 1-4.3 3.6zm1.7-5.6a16 16 0 0 0 0-4h3.4a8 8 0 0 1 0 4z"/></svg>
        www.<span class="accent">moravel</span>.co.nz
      </span>
    </div>

    <div class="social">
      Follow us on:
      <span class="social__dot"></span>
      <span class="social__dot"></span>
    </div>

    <div class="back-tab">Home &amp; Spa Based Treatments</div>
  </section>

</body>
</html>
```